co working space / serviced office/ business centre

Brevlo - brevlo.in, is a very young brand bieng run by 3 young entrepreneurs. We want to be become out of the league company delivering fabulous and beautiful serviced offices in India and abroad. We hire designers who have made spaces across the world. We want to get visiting card design which gives complete fresh look to the people who carries that card, has to be very impactful and should symbolise happy young and energetic brand. should be completely out of the box thinking of international level, should portray global brand image.

Target Market(s)

Startups, (Small, medium and large corporates)

Industry/Entity Type

Business

Contact Information for Business Card

Name, Email, Address, Mobile number, Landline number, website

Colors

Designer to choose colors to be used in the design.

Requirements
Must have
• Nice new shape
Nice to have
• We want creative cuts, different size and impactful brand clarity
Should not have
• Boring and regular design and shape

```html
<!DOCTYPE html>
<html lang="en">
<head>
<meta charset="utf-8">
<title>Brevlo — Business Card</title>
<link href="https://fonts.googleapis.com/css2?family=Open+Sans:wght@400;600;700&display=swap" rel="stylesheet">
<style>
  :root {
    --stage: #2f2f31;
    --ink: #111111;
    --red: #ec2b3a;
    --white: #ffffff;
    --grey: #6b6b6b;
    --text: #1d1d1d;
  }
  * { box-sizing: border-box; margin: 0; padding: 0; }
  html, body {
    width: 1200px; height: 864px; overflow: hidden;
    background: var(--stage);
    font-family: "Open Sans", Arial, sans-serif;
  }
  .stage {
    position: relative; width: 1200px; height: 864px;
    display: flex; flex-direction: column; align-items: center; justify-content: center; gap: 56px;
  }
  .card {
    position: relative; width: 600px; height: 343px;
    border-radius: 22px; overflow: hidden;
    box-shadow: 0 18px 40px rgba(0,0,0,.45);
  }
  /* Back side */
  .card--back { background: var(--ink); }
  .card--back .brand {
    position: absolute; left: 0; right: 0; top: 108px;
    display: flex; flex-direction: column; align-items: center;
  }
  .brand__name {
    display: flex; align-items: center; gap: 14px;
    color: var(--red); font-weight: 700; font-size: 64px; letter-spacing: 6px; line-height: 1;
  }
  .brand__dot { width: 26px; height: 26px; border-radius: 50%; background: var(--red); }
  .brand__rule { width: 320px; height: 3px; background: var(--red); margin-top: 14px; }
  .card--back .web {
    position: absolute; left: 0; right: 0; top: 262px; text-align: center;
    color: var(--white); font-size: 17px; font-weight: 600; letter-spacing: .3px;
  }
  /* Front side */
  .card--front { background: var(--white); }
  .card--front .swoosh { position: absolute; inset: 0; }
  .front-brand { position: absolute; left: 44px; top: 46px; }
  .front-brand .brand__name { font-size: 44px; letter-spacing: 4px; gap: 10px; }
  .front-brand .brand__dot { width: 18px; height: 18px; }
  .front-brand .brand__rule { width: 230px; height: 2px; margin-top: 10px; }
  .person { position: absolute; left: 48px; top: 150px; }
  .person__name { font-size: 24px; font-weight: 600; color: var(--text); line-height: 1.1; }
  .person__role { font-size: 16px; color: var(--grey); margin-top: 2px; }
  .contacts { position: absolute; left: 52px; top: 222px; list-style: none; }
  .contacts li {
    display: flex; align-items: center; gap: 10px;
    font-size: 16px; color: var(--grey); line-height: 24px;
  }
  .contacts svg { width: 14px; height: 14px; fill: var(--red); flex: none; }
  .address {
    position: absolute; right: 30px; bottom: 44px; text-align: left;
    color: var(--white); font-size: 15px; line-height: 21px;
  }
</style>
</head>
<body>
<main class="stage">
  <section class="card card--back" aria-label="Card back">
    <div class="brand">
      <div class="brand__name"><span class="brand__dot"></span>BREVLO</div>
      <div class="brand__rule"></div>
    </div>
    <p class="web">www.brevlo.in</p>
  </section>

  <section class="card card--front" aria-label="Card front">
    <svg class="swoosh" viewBox="0 0 600 343" preserveAspectRatio="none" aria-hidden="true">
      <path d="M300 0 C360 10 384 60 380 120 C374 210 320 290 240 343 L600 343 L600 0 Z" fill="var(--ink)"/>
      <path d="M318 0 C378 14 392 70 386 130 C378 215 324 292 240 343 L600 343 L600 0 Z" fill="var(--white)"/>
      <path d="M330 0 C396 18 398 80 390 140 C380 220 326 294 240 343 L600 343 L600 0 Z" fill="var(--red)"/>
    </svg>

    <div class="front-brand">
      <div class="brand__name"><span class="brand__dot"></span>BREVLO</div>
      <div class="brand__rule"></div>
    </div>

    <div class="person">
      <p class="person__name">Arjun Mehra</p>
      <p class="person__role">President</p>
    </div>

    <ul class="contacts">
      <li><svg viewBox="0 0 16 16"><path d="M3 1l3 3-1.5 2a9 9 0 0 0 5.5 5.5L12 10l3 3-2 2C7 15 1 9 1 3z"/></svg>01 047-218-5530</li>
      <li><svg viewBox="0 0 16 16"><path d="M4 0h8a1 1 0 0 1 1 1v14a1 1 0 0 1-1 1H4a1 1 0 0 1-1-1V1a1 1 0 0 1 1-1zm1 2v10h6V2z"/></svg>01 047-218-5531</li>
      <li><svg viewBox="0 0 16 16"><path d="M0 3h16v10H0zm1.5 1.2L8 9l6.5-4.8V12h-13z"/></svg>hello@brevlo.in</li>
      <li><svg viewBox="0 0 16 16"><path d="M8 0a8 8 0 1 0 0 16A8 8 0 0 0 8 0zm-1 1.6V5H4.3A6.5 6.5 0 0 1 7 1.6zm2 0A6.5 6.5 0 0 1 11.7 5H9zM3.7 6.5H7v3H3.7a6.5 6.5 0 0 1 0-3zm5.3 0h3.3a6.5 6.5 0 0 1 0 3H9zM4.3 11H7v3.4A6.5 6.5 0 0 1 4.3 11zM9 11h2.7A6.5 6.5 0 0 1 9 14.4z"/></svg>www.brevlo.in</li>
    </ul>

    <p class="address">Street Name, Suite 100<br>State, Zip Code, Country</p>
  </section>
</main>
</body>
</html>
```